Business card design for holistic health care clinic

We need a double-sided business card design for our holistic health care clinic that integrates our logo design and also its color scheme. My business is called Valmira. It is an integrative medicine clinic. You have already done the logo for me. Please ensure an elegant and upscale design that is not cluttered, but still has all the necessary information (please see below for details).

Target Market(s)

Wellness, fitness, rehabilitation for educated, well-traveled open-minded clients who are focused on natural, organic, balanced and preventive healthcare and lifestyle.

Industry/Entity Type

Medical

Contact Information for Business Card

Modern, clean.

Number of Pages Required

1 page

Font styles to use
Serif
Sans Serif

Colors

Designer to choose colors to be used in the design.

Requirements
Must have
• Logo on one side, all other information on the other side.
• Other information should include:
• Tobias Wrenfeld - DOE, CPT, LMT
• 4100 East Marrow Drive
• Austin, TX 78119
• 512 555 0148
• 818 555 0192
• info@ValmiraHealth.example
• t.wrenfeld@ValmiraHealth.example
Nice to have
• Darker background on front - but not totally black - shaded/dark gray.

```html
<!DOCTYPE html>
<html lang="en">
<head>
<meta charset="UTF-8">
<title>Valmira Business Card</title>
<link href="https://fonts.googleapis.com/css2?family=Nunito:wght@800&family=Roboto:ital,wght@0,400;1,400&family=Roboto+Condensed:wght@700&display=swap" rel="stylesheet">
<style>
  :root {
    --backdrop: #e4e4e4;
    --card-dark: #262727;
    --card-dark-light: #333434;
    --brand-blue: #0a93cf;
    --text-light: #ffffff;
    --rule: #8a8a8a;
  }
  * { margin: 0; padding: 0; box-sizing: border-box; }
  html, body { width: 1200px; height: 960px; overflow: hidden; }
  body { background: var(--backdrop); position: relative; font-family: "Roboto", Arial, sans-serif; }

  .card {
    position: absolute;
    width: 600px;
    height: 343px;
    overflow: hidden;
    background: linear-gradient(135deg, var(--card-dark) 0%, var(--card-dark-light) 100%);
  }
  .card--front { left: 314px; top: 113px; }
  .card--back { left: 311px; top: 472px; background: var(--card-dark); }

  .front-wave { position: absolute; inset: 0; }

  .brand-name {
    font-family: "Nunito", Arial, sans-serif;
    font-weight: 800;
    color: var(--brand-blue);
    letter-spacing: 1px;
    line-height: 1;
  }
  .card--front .brand-name {
    position: absolute; right: 40px; top: 78px; font-size: 50px;
  }
  .card--back .brand-name {
    position: absolute; left: 0; right: 0; top: 138px; text-align: center; font-size: 66px;
  }

  .holder { position: absolute; right: 40px; top: 158px; text-align: right; font-family: "Roboto Condensed", Arial, sans-serif; font-weight: 700; color: var(--brand-blue); }
  .holder-name { font-size: 21px; text-transform: uppercase; line-height: 1.1; }
  .holder-credentials { font-size: 12px; margin-top: 2px; }

  .contact { position: absolute; left: 36px; top: 205px; color: var(--text-light); font-size: 14.5px; }
  .contact-list { list-style: none; }
  .contact-item { display: flex; align-items: center; height: 19px; }
  .contact-icon { width: 13px; height: 13px; margin-right: 10px; fill: var(--card-dark); }
  .contact-address { margin-top: 9px; }

  .tagline {
    position: absolute; left: 0; right: 0; top: 285px;
    display: flex; align-items: center; justify-content: center; gap: 6px;
    color: var(--text-light); font-style: italic; font-size: 17px;
  }
  .tagline-rule { width: 110px; height: 1px; }
  .tagline-rule--left { background: linear-gradient(90deg, transparent, var(--rule)); }
  .tagline-rule--right { background: linear-gradient(90deg, var(--rule), transparent); }
</style>
</head>
<body>

<section class="card card--front">
  <svg class="front-wave" viewBox="0 0 600 343" width="600" height="343" aria-hidden="true">
    <path d="M0 0 H120 C150 60 215 95 228 150 C238 195 205 220 232 262 C262 305 335 332 425 343 H0 Z" fill="var(--brand-blue)"/>
  </svg>

  <div class="brand-name">VALMIRA</div>

  <div class="holder">
    <div class="holder-name">Tobias Wrenfeld</div>
    <div class="holder-credentials">DOE, CPT, LMT</div>
  </div>

  <div class="contact">
    <ul class="contact-list">
      <li class="contact-item">
        <svg class="contact-icon" viewBox="0 0 24 24"><path d="M6.6 10.8a15.1 15.1 0 0 0 6.6 6.6l2.2-2.2a1 1 0 0 1 1-.25 11.4 11.4 0 0 0 3.6.57 1 1 0 0 1 1 1V20a1 1 0 0 1-1 1A17 17 0 0 1 3 4a1 1 0 0 1 1-1h3.5a1 1 0 0 1 1 1c0 1.25.2 2.45.57 3.57a1 1 0 0 1-.25 1z"/></svg>
        512 555 0148
      </li>
      <li class="contact-item">
        <svg class="contact-icon" viewBox="0 0 24 24"><path d="M7 1h10a2 2 0 0 1 2 2v18a2 2 0 0 1-2 2H7a2 2 0 0 1-2-2V3a2 2 0 0 1 2-2zm0 3v14h10V4zm5 15.5a1 1 0 1 0 0 2 1 1 0 0 0 0-2z"/></svg>
        818 555 0192
      </li>
      <li class="contact-item">
        <svg class="contact-icon" viewBox="0 0 24 24"><path d="M2 5h20v14H2zm2 2v.5l8 5 8-5V7l-8 5z"/></svg>
        t.wrenfeld@ValmiraHealth.example
      </li>
      <li class="contact-item">
        <svg class="contact-icon" viewBox="0 0 24 24"><path d="M12 2a10 10 0 1 0 0 20 10 10 0 0 0 0-20zm-1 17.9A8 8 0 0 1 4.2 10.2L9 15v1a2 2 0 0 0 2 2zm6.9-2.5A2 2 0 0 0 16 16h-1v-3a1 1 0 0 0-1-1H8v-2h2a1 1 0 0 0 1-1V7h2a2 2 0 0 0 2-2v-.4a8 8 0 0 1 2.9 12.8z"/></svg>
        www.ValmiraHealth.example
      </li>
    </ul>
    <p class="contact-address">4100 East Marrow Drive , Austin, TX 78119</p>
  </div>
</section>

<section class="card card--back">
  <div class="brand-name">VALMIRA</div>
  <div class="tagline">
    <span class="tagline-rule tagline-rule--left"></span>
    <span class="tagline-text">helping the body help itself</span>
    <span class="tagline-rule tagline-rule--right"></span>
  </div>
</section>

</body>
</html>
```